Moravel Aesthetic Doctor

I require an elegant, luxurious looking business card for my aesthetic business. I am a doctor and that will set me aside from competitors. I am planning to provide home and spa based treatments to clients with high expectations. I have attached my logo.

```html
<!DOCTYPE html>
<html lang="en">
<head>
<meta charset="utf-8">
<title>Moravel Aesthetic Doctor – Business Card</title>
<link rel="stylesheet" href="https://fonts.googleapis.com/css2?family=Roboto:wght@300;400;500&display=swap">
<style>
  :root{
    --bg:#2b2b2d;
    --card:#333335;
    --edge:#7cc7ec;
    --accent:#5fbde8;
    --text:#d4d4d6;
    --muted:#a8a8ab;
    --rule:#6a6a6d;
    --silhouette-a:#4a4a4d;
    --silhouette-b:#2e2e30;
  }
  *{box-sizing:border-box;margin:0;padding:0}
  html,body{width:1200px;height:1108px;overflow:hidden;background:var(--bg);font-family:"Roboto",Arial,sans-serif}
  .card{
    position:absolute;left:160px;width:880px;height:503px;
    background:var(--card);
    border-bottom:6px solid var(--edge);
    box-shadow:0 10px 28px rgba(0,0,0,.45);
    overflow:hidden;
  }
  .card--contact{top:40px}
  .card--services{top:565px}

  /* brand lockup */
  .brand{display:flex;align-items:center;gap:22px}
  .brand__dot{width:78px;height:78px;border-radius:50%;background:var(--accent);flex:none}
  .brand__name{color:var(--text);font-weight:300;font-size:34px;letter-spacing:4px;text-transform:uppercase;line-height:1.15}

  /* contact side */
  .card--contact .brand{position:absolute;left:64px;top:70px}
  .social{position:absolute;right:56px;top:60px;display:flex;gap:18px}
  .social span{width:24px;height:24px;border-radius:50%;border:2px solid var(--accent)}
  .divider{position:absolute;left:64px;right:64px;top:232px;height:2px;background:var(--rule)}
  .person{position:absolute;left:64px;top:270px}
  .person__name{color:var(--accent);font-size:32px;font-weight:400}
  .person__name small{font-size:15px;letter-spacing:.5px}
  .person__role{color:var(--muted);font-size:20px;font-weight:300;margin-top:8px}
  .person__rule{width:370px;height:2px;background:var(--rule);margin:14px 0 14px}
  .contacts{list-style:none}
  .contacts li{display:flex;align-items:center;gap:14px;color:var(--text);font-size:20px;font-weight:300;margin-bottom:8px}
  .contacts svg{width:20px;height:20px;flex:none}

  /* services side */
  .portrait{
    position:absolute;left:-70px;top:40px;width:560px;height:560px;border-radius:50%;
    background:radial-gradient(circle at 65% 35%,var(--silhouette-a),var(--silhouette-b) 70%);
    box-shadow:inset 0 0 0 6px #48484b;
  }
  .services{position:absolute;left:530px;top:56px}
  .services .brand__name{font-size:32px}
  .services__list{list-style:none;margin-top:34px}
  .services__list li{color:var(--text);font-size:22px;font-weight:300;line-height:1.55;position:relative;padding-left:22px}
  .services__list li::before{content:"";position:absolute;left:0;top:14px;width:8px;height:8px;border-radius:50%;background:var(--accent)}
  .services__list li.cont::before{display:none}
</style>
</head>
<body>

<section class="card card--contact">
  <div class="brand">
    <span class="brand__dot"></span>
    <div class="brand__name">Moravel<br>Aesthetic Doctor</div>
  </div>
  <div class="social" aria-label="Social links"><span></span><span></span></div>
  <div class="divider"></div>
  <div class="person">
    <p class="person__name">Dr Elise Varnor, <small>MRCPCH MD</small></p>
    <p class="person__role">Australasian Diploma of Aesthetic Medicine</p>
    <div class="person__rule"></div>
    <ul class="contacts">
      <li><svg viewBox="0 0 24 24" fill="none" stroke="var(--accent)" stroke-width="2"><path d="M5 3h4l2 5-3 2a12 12 0 0 0 6 6l2-3 5 2v4a2 2 0 0 1-2 2A17 17 0 0 1 3 5a2 2 0 0 1 2-2z"/></svg>0800 555 014</li>
      <li><svg viewBox="0 0 24 24" fill="none" stroke="var(--accent)" stroke-width="2"><rect x="3" y="5" width="18" height="14" rx="1"/><path d="M3 6l9 7 9-7"/></svg>elise@moravel.co.nz</li>
      <li><svg viewBox="0 0 24 24" fill="none" stroke="var(--accent)" stroke-width="2"><circle cx="12" cy="12" r="9"/><path d="M3 12h18M12 3c3 3 3 15 0 18M12 3c-3 3-3 15 0 18"/></svg>www.moravel.co.nz</li>
    </ul>
  </div>
</section>

<section class="card card--services">
  <div class="portrait" role="img" aria-label="Large soft silhouette illustration of a woman in profile with flowing hair inside a circle"></div>
  <div class="services">
    <div class="brand__name">Moravel<br>Aesthetic Doctor</div>
    <ul class="services__list">
      <li>Dermal injectables</li>
      <li>Plasma facials</li>
      <li>Microneedling</li>
      <li>Skin boosters</li>
      <li>Excessive sweating</li>
      <li>Home and Spa Based</li>
      <li class="cont">Treatments</li>
    </ul>
  </div>
</section>

</body>
</html>
```